Elegant One-Page Flyer That Catches People's Eye

For a series of workshops and zoom calls I am marketing with a colleague of mine, we would like to have an elegant, catchy one-page flyer that entices people to contact us. I am envisioning a one-page flyer (a card that is somewhat larger than a postcard) with great text, layout and images which magnetically draws people to us and is positive and inspiring. Also, if at all possible, a QR code linking it to our websites. Good colours would be shades of blue and green. I am uploading: the Text, our pictures, logos and contact information.

```html
<!DOCTYPE html>
<html lang="en">
<head>
<meta charset="utf-8">
<title>Rising Above Hidden Career Deal Breakers</title>
<link href="https://fonts.googleapis.com/css2?family=Bebas+Neue&family=Poppins:wght@400;500;600;700&display=swap" rel="stylesheet">
<style>
  :root{
    --ink:#1e1e1e;
    --card:#0b0b0b;
    --green:#7f9f55;
    --green-bright:#8fc04a;
    --green-text:#92b865;
    --white:#ffffff;
    --muted:#e9e9e9;
    --dark:#151515;
  }
  *{margin:0;padding:0;box-sizing:border-box}
  html,body{width:1200px;height:2327px;overflow:hidden;background:var(--ink)}
  body{font-family:'Poppins',sans-serif;color:var(--white)}
  .flyer{position:relative;width:1200px;height:2327px;overflow:hidden;background:var(--ink)}
  .hero-photo{
    position:absolute;left:0;top:0;width:1200px;height:1150px;
    background:
      radial-gradient(ellipse 520px 260px at 420px 690px, rgba(205,140,80,.75), rgba(205,140,80,0) 70%),
      radial-gradient(ellipse 420px 600px at 900px 420px, rgba(70,52,42,.85), rgba(70,52,42,0) 70%),
      linear-gradient(180deg,#6c767c 0%,#767570 30%,#8c7256 55%,#4a3c30 78%,var(--ink) 100%);
  }
  .abs{position:absolute}
  .kicker{left:83px;top:88px;font-weight:700;font-size:44px;line-height:46px;text-transform:uppercase}
  .kicker-sub{left:83px;top:212px;font-size:30px;line-height:36px;color:var(--muted);width:560px}
  .headline{left:83px;top:370px;font-family:'Bebas Neue',sans-serif;font-size:98px;line-height:88px;color:#f4f4f4;font-weight:400}
  .offer{left:83px;top:556px;width:1041px;height:122px;display:flex}
  .offer-main{width:510px;height:122px;background:var(--green);border-radius:61px 0 0 61px;
    font-family:'Bebas Neue',sans-serif;font-size:68px;line-height:124px;padding-left:22px;white-space:nowrap}
  .offer-plus{position:absolute;left:492px;top:30px;font-size:56px;font-weight:700;line-height:56px;color:var(--dark)}
  .offer-extra{flex:1;background:var(--white);border-radius:0 61px 61px 0;color:#111;font-weight:600;
    font-size:29px;line-height:35px;padding:26px 0 0 46px;white-space:nowrap}
  .learn{left:86px;top:708px;font-weight:700;font-size:31px;line-height:39px}
  .learn em{font-style:normal;color:var(--green-text)}
  .topics{left:86px;top:768px;width:1030px;height:224px;border:2px dashed rgba(143,192,74,.6);border-top:none;border-radius:0 0 12px 12px}
  .topics-top{position:absolute;left:770px;top:768px;width:346px;border-top:2px dashed rgba(143,192,74,.6)}
  .topic{position:absolute;display:flex;gap:18px;font-size:27px;line-height:32px;color:var(--muted)}
  .topic svg{flex:none;margin-top:6px}
  .section-title{left:0;top:1025px;width:1200px;text-align:center;font-weight:600;font-size:40px;letter-spacing:6px}
  .facilitator{position:absolute;left:121px;width:986px;height:322px;background:var(--card);
    border:3px solid var(--green-bright);border-radius:161px}
  .portrait{position:absolute;left:12px;top:12px;width:292px;height:292px;border-radius:50%;
    border:5px solid var(--white);background:radial-gradient(circle at 50% 40%,#d9d2cc,#b9b0a8 60%,#8c8580)}
  .facilitator h3{position:absolute;left:322px;top:38px;font-weight:700;font-size:42px;color:var(--green-text);white-space:nowrap}
  .facilitator p{position:absolute;left:322px;top:104px;font-size:28px;line-height:34px;white-space:nowrap}
  .brand{font-weight:500;font-size:44px;line-height:50px;color:var(--green-text);display:flex;align-items:center;gap:18px;white-space:nowrap}
  .brand-dot{width:24px;height:24px;border-radius:50%;background:var(--green-text)}
  .brand-alt{color:var(--white);font-size:40px}
  .contact-box{left:71px;top:2018px;width:1062px;height:247px;background:#0e0e0e;border-radius:26px}
  .contact-tab{left:268px;top:2004px;width:696px;height:82px;background:var(--green);border-radius:0 0 40px 40px;
    text-align:center;font-weight:700;font-size:29px;line-height:35px;padding-top:6px}
  .contact{position:absolute;top:2110px;font-weight:600;font-size:27px;line-height:34px;white-space:nowrap}
  .contact .who{color:var(--green-text);font-size:24px;font-weight:700;margin-bottom:4px}
  .contact .line{display:flex;align-items:center;gap:14px}
  .divider{left:531px;top:2104px;height:110px;border-left:2px dashed rgba(255,255,255,.5)}
</style>
</head>
<body>
<main class="flyer">
  <div class="hero-photo" role="img" aria-label="Silhouette of a climber with a backpack scaling a rock face at sunset"></div>

  <h2 class="abs kicker">Is your career going<br>the way you want?</h2>
  <p class="abs kicker-sub">If not, do you feel stuck? Blocked? Frustrated? Don’t know what to do about this?</p>

  <h1 class="abs headline">Rising above hidden<br>career deal breakers</h1>

  <div class="abs offer">
    <div class="offer-main">4 Mini-Workshops</div>
    <div class="offer-plus">+</div>
    <div class="offer-extra">2 short Online Group Coaching<br>Sessions between Workshops</div>
  </div>

  <p class="abs learn">Learn to overcome and rise above<br>the <em>4 top hidden career deal breakers fast</em></p>
  <div class="abs topics"></div>
  <div class="topics-top"></div>

  <div class="topic" style="left:110px;top:822px">
    <svg width="20" height="20" viewBox="0 0 20 20"><circle cx="10" cy="10" r="8.5" fill="none" stroke="#8fc04a" stroke-width="1.6"/><path d="M6 10.3l2.7 2.6L14 7.4" fill="none" stroke="#8fc04a" stroke-width="1.8"/></svg>
    <span>Microaggressions</span></div>
  <div class="topic" style="left:110px;top:884px">
    <svg width="20" height="20" viewBox="0 0 20 20"><circle cx="10" cy="10" r="8.5" fill="none" stroke="#8fc04a" stroke-width="1.6"/><path d="M6 10.3l2.7 2.6L14 7.4" fill="none" stroke="#8fc04a" stroke-width="1.8"/></svg>
    <span>Workplace snakes and<br>other dysfunctional types</span></div>
  <div class="topic" style="left:595px;top:826px">
    <svg width="20" height="20" viewBox="0 0 20 20"><circle cx="10" cy="10" r="8.5" fill="none" stroke="#8fc04a" stroke-width="1.6"/><path d="M6 10.3l2.7 2.6L14 7.4" fill="none" stroke="#8fc04a" stroke-width="1.8"/></svg>
    <span>Toxic black box team dynamics</span></div>
  <div class="topic" style="left:595px;top:888px">
    <svg width="20" height="20" viewBox="0 0 20 20"><circle cx="10" cy="10" r="8.5" fill="none" stroke="#8fc04a" stroke-width="1.6"/><path d="M6 10.3l2.7 2.6L14 7.4" fill="none" stroke="#8fc04a" stroke-width="1.8"/></svg>
    <span>Disempowering Subconscious<br>Algorithms</span></div>

  <h2 class="abs section-title">FACILITATORS</h2>

  <section class="facilitator" style="top:1094px">
    <div class="portrait" role="img" aria-label="Portrait photo of Dr. Nora Whitcombe"></div>
    <h3>Dr. Nora Whitcombe</h3>
    <p>PhD, CPC, is an American &amp; Swiss-Trained<br>Work &amp; Organizational Psychologist,<br>ICF-Certified Coach, Board Certified<br>Hypnotherapist, Certified Naturopath (TEN)<br>&amp; Certified Ayurvedic Practitioner.</p>
  </section>

  <section class="facilitator" style="top:1451px">
    <div class="portrait" role="img" aria-label="Portrait photo of Dr. Elena Marchetti"></div>
    <h3 style="top:60px">Dr. Elena Marchetti</h3>
    <p style="top:126px">Ph.D., PCC is a coach and somatic<br>experience practitioner, a team coach<br>with diploma and a certified virtual<br>team coach.</p>
  </section>

  <div class="abs brand" style="left:128px;top:1858px"><span class="brand-dot"></span>Quillmere</div>
  <div class="abs brand brand-alt" style="left:690px;top:1862px">MarchettiCoaching</div>

  <div class="abs contact-box"></div>
  <div class="abs contact-tab">For dates, venue and further information<br>Contact Elena or Nora at</div>

  <div class="contact" style="left:180px">
    <div class="who">DR. NORA WHITCOMBE</div>
    <div class="line"><svg width="20" height="20" viewBox="0 0 24 24"><path d="M6.6 10.8a15 15 0 006.6 6.6l2.2-2.2c.3-.3.7-.4 1-.2 1.1.4 2.3.6 3.6.6.6 0 1 .4 1 1V20c0 .6-.4 1-1 1A17 17 0 013 4c0-.6.4-1 1-1h3.5c.6 0 1 .4 1 1 0 1.3.2 2.5.6 3.6.1.3 0 .7-.2 1z" fill="#8fc04a"/></svg>076 555 0142</div>
    <div class="line"><svg width="20" height="16" viewBox="0 0 24 18"><rect x="1" y="1" width="22" height="16" rx="2" fill="#8fc04a"/><path d="M2 2l10 8 10-8" fill="none" stroke="#0e0e0e" stroke-width="2"/></svg>nora@quillmere.ch</div>
  </div>
  <div class="abs divider"></div>
  <div class="contact" style="left:618px">
    <div class="who">DR. ELENA MARCHETTI</div>
    <div class="line"><svg width="20" height="20" viewBox="0 0 24 24"><path d="M6.6 10.8a15 15 0 006.6 6.6l2.2-2.2c.3-.3.7-.4 1-.2 1.1.4 2.3.6 3.6.6.6 0 1 .4 1 1V20c0 .6-.4 1-1 1A17 17 0 013 4c0-.6.4-1 1-1h3.5c.6 0 1 .4 1 1 0 1.3.2 2.5.6 3.6.1.3 0 .7-.2 1z" fill="#8fc04a"/></svg>079 555 02 87</div>
    <div class="line"><svg width="20" height="16" viewBox="0 0 24 18"><rect x="1" y="1" width="22" height="16" rx="2" fill="#8fc04a"/><path d="M2 2l10 8 10-8" fill="none" stroke="#0e0e0e" stroke-width="2"/></svg>elena@marchetticoaching.ch</div>
  </div>
</main>
</body>
</html>
```